Business Card Design Project

Business card based on attached logo

Todd Merrick
Todd@lorvantest.com
877-514-9073 ext. 318
Www.LorvanTest.com

Industry/Entity Type

Business

```html
<!DOCTYPE html>
<html lang="en">
<head>
<meta charset="utf-8">
<title>Lorvan Test – Business Cards</title>
<link rel="stylesheet" href="https://fonts.googleapis.com/css2?family=Arimo:wght@400;700&display=swap">
<style>
  :root{
    --stage:#8b8d90;
    --red:#e0242b;
    --red-dark:#c21f25;
    --red-bright:#ef3a3f;
    --ink:#231f20;
    --charcoal:#2b2b2b;
    --paper:#f4f4f4;
    --paper-shade:#dcdcdc;
    --white:#ffffff;
  }
  *{margin:0;padding:0;box-sizing:border-box}
  html,body{width:1200px;height:720px;overflow:hidden;background:var(--stage)}
  body{font-family:"Arimo",Arial,sans-serif;position:relative}

  .card{position:absolute;width:565px;height:322px;overflow:hidden}
  .card--contact{left:27px;top:26px;background:linear-gradient(90deg,var(--paper) 0%,#ffffff 50%,var(--paper-shade) 100%)}
  .card--red{left:612px;top:26px;background:linear-gradient(135deg,var(--red) 0%,var(--red-dark) 100%)}
  .card--light{left:27px;top:372px;background:linear-gradient(90deg,var(--paper-shade) 0%,#f6f6f6 45%,var(--paper-shade) 100%)}
  .card--dark{left:612px;top:372px;background:radial-gradient(circle at 50% 40%,#3a3a3a 0%,#1f1f1f 75%)}

  .wave{position:absolute;left:0;top:0;width:565px;height:322px}

  .brand{position:absolute;font-weight:700;line-height:1;text-transform:uppercase}
  .brand__main{display:block;letter-spacing:-1px}
  .brand__sub{display:block;letter-spacing:.28em}

  .card--contact .brand{left:48px;top:58px;color:var(--ink)}
  .card--contact .brand__main{font-size:56px}
  .card--contact .brand__sub{font-size:34px;margin-top:8px;padding-left:14px}

  .holder-name{position:absolute;right:36px;top:45px;color:var(--red);font-size:19px;text-transform:uppercase;letter-spacing:.02em}

  .contact-list{position:absolute;right:26px;top:238px;list-style:none;color:var(--white);font-size:17px;text-align:right}
  .contact-list li{height:28px;display:flex;align-items:center;justify-content:flex-end;gap:7px}
  .contact-list svg{width:13px;height:13px;flex:none}

  .card--red .brand{left:34px;top:30px;color:var(--white)}
  .card--red .brand__main{font-size:94px}
  .card--red .brand__sub{font-size:52px;margin-top:18px;padding-left:22px}
  .faint-square{position:absolute;right:0;top:158px;width:140px;height:140px;background:rgba(255,255,255,.12)}

  .card--light .mark{position:absolute;left:193px;top:54px;width:180px;height:180px;background:var(--red-bright)}

  .card--dark .brand{left:0;right:0;top:78px;text-align:center;color:var(--white)}
  .card--dark .brand__main{font-size:78px}
  .card--dark .brand__sub{font-size:48px;margin-top:14px;padding-left:.28em}

  .site{position:absolute;font-size:17px;letter-spacing:.18em}
  .card--red .site{left:36px;top:303px;color:var(--white);line-height:1}
  .card--light .site{left:0;right:0;top:278px;text-align:center;color:var(--ink);line-height:1}
  .card--dark .site{left:0;right:0;top:282px;text-align:center;color:var(--white);line-height:1}
</style>
</head>
<body>

<section class="card card--contact">
  <svg class="wave" viewBox="0 0 565 322" aria-hidden="true">
    <path d="M0 258 C140 300 330 190 565 146 L565 164 C340 200 160 300 0 276 Z" fill="#e0242b"/>
    <path d="M0 282 C160 318 350 205 565 168 L565 322 L0 322 Z" fill="#2b2b2b"/>
    <path d="M0 290 C170 318 360 215 565 178" fill="none" stroke="#ffffff" stroke-width="2"/>
    <path d="M30 314 C190 320 360 230 540 186" fill="none" stroke="#555" stroke-width="1.5"/>
  </svg>
  <div class="brand"><span class="brand__main">Lorvan</span><span class="brand__sub">Test</span></div>
  <p class="holder-name">Todd Merrick</p>
  <ul class="contact-list">
    <li><svg viewBox="0 0 16 16"><path d="M4 1 L6.5 5 L5 6.5 C6 8.5 7.5 10 9.5 11 L11 9.5 L15 12 L13 15 C7 15 1 9 1 3 Z" fill="#fff"/></svg>877-514-9073 ext. 318</li>
    <li><svg viewBox="0 0 16 16"><rect x="1" y="4" width="14" height="10" fill="#fff"/><path d="M1 4 L8 10 L15 4" fill="none" stroke="#2b2b2b" stroke-width="1.4"/></svg>Todd@lorvantest.com</li>
    <li><svg viewBox="0 0 16 16"><circle cx="8" cy="8" r="6.5" fill="none" stroke="#fff" stroke-width="1.4"/><ellipse cx="8" cy="8" rx="2.8" ry="6.5" fill="none" stroke="#fff" stroke-width="1.2"/><path d="M1.5 8 H14.5" stroke="#fff" stroke-width="1.2"/></svg>www.lorvantest.com</li>
  </ul>
</section>

<section class="card card--red">
  <div class="brand"><span class="brand__main">Lorvan</span><span class="brand__sub">Test</span></div>
  <div class="faint-square" aria-hidden="true"></div>
  <p class="site">www.lorvantest.com</p>
</section>

<section class="card card--light">
  <div class="mark" aria-hidden="true"></div>
  <p class="site">www.lorvantest.com</p>
</section>

<section class="card card--dark">
  <div class="brand"><span class="brand__main">Lorvan</span><span class="brand__sub">Test</span></div>
  <p class="site">www.lorvantest.com</p>
</section>

</body>
</html>
```